Employee Benefits and Insurance Consulting

We are an existing company with over 30 years experience but are changing our name. We would like a simple design with grey tones.

Industry/Entity Type

Insurance

Contact Information for Business Card

Marlow Benefits Consulting
Gerald P Hollins CEO
5172 Brackenridge Road
Louisville, TN 37777
gerald@marlowbenefits-example.com
865-412-5593 - O
865-247-3861 - C

```html
<!DOCTYPE html>
<html lang="en">
<head>
<meta charset="utf-8">
<title>Marlow Benefits Consulting – Business Card</title>
<link rel="stylesheet" href="https://fonts.googleapis.com/css2?family=Source+Sans+3:wght@400;600&display=swap">
<style>
  :root {
    --bg: #3a3634;
    --card: #1b1b1c;
    --card-glow: #2e2e30;
    --red: #d9161c;
    --white: #f2f2f2;
    --grey-line: #5a5a5c;
    --font: "Source Sans 3", "Myriad Pro", Arial, sans-serif;
  }
  * { box-sizing: border-box; margin: 0; padding: 0; }
  html, body {
    width: 1200px; height: 844px; overflow: hidden;
    background: var(--bg);
    font-family: var(--font);
  }
  .stage {
    width: 1200px; height: 844px;
    display: flex; align-items: center; justify-content: center;
    gap: 48px;
  }
  .card {
    position: relative;
    width: 532px; height: 304px;
    background: var(--card);
    overflow: hidden;
    box-shadow: 0 10px 24px rgba(0,0,0,.45);
  }

  /* Contact side */
  .card--contact .band {
    position: absolute; left: 0; right: 0; height: 13px;
    background: var(--red);
  }
  .card--contact .band--top { top: 0; }
  .card--contact .band--bottom { bottom: 0; }
  .contact {
    position: absolute; left: 0; right: 0; top: 64px;
    text-align: center; color: var(--white);
  }
  .contact__name {
    color: var(--red); font-size: 19px; font-weight: 400;
    letter-spacing: .5px; text-transform: uppercase;
    margin-bottom: 16px;
  }
  .contact__title { font-size: 13px; }
  .contact__line { font-size: 15px; line-height: 21px; }
  .contact__address {
    position: absolute; left: 0; right: 0; bottom: 52px;
    text-align: center; color: var(--white); font-size: 15px;
  }

  /* Brand side */
  .card--brand {
    background: radial-gradient(ellipse at 50% 40%, var(--card-glow) 0%, var(--card) 62%);
  }
  .tab {
    position: absolute; width: 26px; height: 40px;
    background: var(--red);
  }
  .tab::after {
    content: ""; position: absolute; top: 0; bottom: 0; width: 5px;
    background: var(--white);
  }
  .tab--right { right: 0; top: 30px; }
  .tab--right::after { left: 0; }
  .tab--left { left: 0; top: 168px; }
  .tab--left::after { right: 0; }
  .brand {
    position: absolute; left: 0; right: 0; top: 118px;
    display: flex; flex-direction: column; align-items: center;
  }
  .brand__row { display: flex; align-items: center; gap: 12px; }
  .brand__mark { width: 16px; height: 16px; background: var(--red); }
  .brand__name {
    color: var(--red); font-size: 30px; font-weight: 600;
    letter-spacing: .2px;
  }
  .brand__rule {
    width: 300px; height: 1px; margin-top: 12px;
    background: var(--grey-line);
  }
</style>
</head>
<body>
  <main class="stage">
    <section class="card card--contact" aria-label="Business card contact side">
      <div class="band band--top"></div>
      <div class="contact">
        <p class="contact__name">Gerald P Hollins <span class="contact__title">- CEO</span></p>
        <p class="contact__line">865-247-3861</p>
        <p class="contact__line">865-412-5593</p>
        <p class="contact__line">gerald@marlowbenefits-example.com</p>
      </div>
      <p class="contact__address">5172 Brackenridge Road Louisville, TN 37777</p>
      <div class="band band--bottom"></div>
    </section>

    <section class="card card--brand" aria-label="Business card brand side">
      <div class="tab tab--right"></div>
      <div class="tab tab--left"></div>
      <div class="brand">
        <div class="brand__row">
          <span class="brand__mark"></span>
          <span class="brand__name">Marlow Benefits Consulting</span>
        </div>
        <div class="brand__rule"></div>
      </div>
    </section>
  </main>
</body>
</html>
```